Meridale Partners Website

Meridale Partners (MP) provide Analytics & Enterprise Performance Management (EPM) advisory & consultancy services. We are passionate about data and making a difference for our clients by working in partnership with them, helping them on their journey to becoming an Meridale Partner. We deliver insights which give our clients a competitive edge and a much deeper understanding of their organisation.

We need a website which shows who we are, what we do and how we do it.

www.meridale-partners.example is our very basic website at the moment. We want to completely revamp it with a corporate look

```html
<!DOCTYPE html>
<html lang="en">
<head>
<meta charset="utf-8">
<title>Meridale Partners</title>
<link rel="stylesheet" href="https://fonts.googleapis.com/css2?family=Montserrat:wght@500;600;700;800&family=Roboto:wght@400;500&display=swap">
<style>
:root{
  --navy:#2c5672;
  --navy-dark:#234a63;
  --orange:#e8873e;
  --ink:#2b2b2b;
  --muted:#555;
  --black:#000;
  --white:#fff;
  --grey:#8fa3b1;
}
*{margin:0;padding:0;box-sizing:border-box}
html,body{width:1200px;height:3072px;overflow:hidden;background:var(--white)}
body{position:relative;font-family:'Roboto',sans-serif;color:var(--ink)}
.abs{position:absolute}
.head-font{font-family:'Montserrat',sans-serif}

/* top bar */
.topbar{left:0;top:0;width:1200px;height:43px}
.topbar-item{top:0;height:43px;display:flex;align-items:center;gap:12px;color:var(--white);font-size:15px;font-weight:500}
.icon-dot{width:32px;height:32px;border-radius:50%;background:var(--white);display:flex;align-items:center;justify-content:center}
.divider{left:880px;top:10px;width:1px;height:24px;background:rgba(255,255,255,.6)}

/* header */
.brand{left:117px;top:36px;display:flex;align-items:center;gap:16px}
.brand-mark{width:78px;height:78px;border-radius:50%;background:var(--navy)}
.brand-name{font-family:'Montserrat',sans-serif;font-weight:700;font-size:31px;line-height:36px;color:var(--navy);letter-spacing:.5px}
.nav{top:84px;font-size:15.5px;font-weight:500;color:var(--ink)}
.login{left:978px;top:74px;width:110px;height:39px;border:2px solid var(--orange);border-radius:20px;color:var(--orange);font-family:'Montserrat',sans-serif;font-weight:600;font-size:16px;display:flex;align-items:center;justify-content:center}

/* hero */
.hero{left:0;top:138px;width:1200px;height:720px}
.hero-welcome{left:110px;top:247px;font-family:'Montserrat',sans-serif;font-weight:600;font-size:33px;color:var(--orange)}
.hero-title{left:108px;top:300px;font-family:'Montserrat',sans-serif;font-weight:800;font-size:62px;line-height:78px;color:var(--navy)}
.hero-sub{left:110px;top:464px;font-size:16px;font-weight:500;color:var(--ink)}
.btn{border-radius:30px;font-family:'Montserrat',sans-serif;font-weight:700;color:var(--white);display:flex;align-items:center;justify-content:center}
.btn-start{left:111px;top:515px;width:154px;height:40px;background:var(--orange);font-size:15.5px}
.dot{top:791px;width:13px;height:13px;border-radius:50%;background:var(--white)}

/* who we are */
.who-circle{left:-72px;top:805px;width:406px;height:406px;border-radius:50%;background:var(--orange)}
.who-photo{left:111px;top:928px;width:466px;height:364px;background:linear-gradient(135deg,#3a3e46 0%,#6b5648 45%,#2d3138 100%)}
.who-title{left:644px;top:960px;font-family:'Montserrat',sans-serif;font-weight:600;font-size:33px;color:var(--ink);display:flex;align-items:center;gap:14px}
.who-title span.rule{display:inline-block;width:50px;height:4px;background:var(--navy);margin-top:14px}
.who-text{left:644px;top:1031px;width:417px;font-size:16px;line-height:25.7px;color:var(--ink);text-align:justify}
.btn-learn{left:644px;top:1195px;width:151px;height:57px;background:var(--navy);font-size:16px}

/* what we do */
.what{left:0;top:1379px;width:1200px;height:642px;background:linear-gradient(160deg,var(--navy) 0%,#2f5a77 60%,#27506b 100%)}
.section-title{width:1200px;left:0;text-align:center;font-family:'Montserrat',sans-serif;font-weight:600;font-size:33px}
.title-rule{left:576px;width:48px;height:4px}
.card{top:1586px;width:299px;height:341px;overflow:hidden}
.card-photo{position:absolute;inset:0}
.card-shade{position:absolute;left:0;right:0;bottom:0;height:170px;background:linear-gradient(to bottom,rgba(0,0,0,0),rgba(0,0,0,.55))}
.card-shade.active{background:linear-gradient(to bottom,rgba(232,135,62,0),rgba(232,135,62,.95))}
.card-name{position:absolute;left:0;right:0;top:218px;text-align:center;font-family:'Montserrat',sans-serif;font-weight:600;font-size:23px;color:var(--white)}
.card-link{position:absolute;left:0;right:0;top:266px;text-align:center;font-family:'Montserrat',sans-serif;font-weight:700;font-size:15px;color:var(--white)}
.arrow-btn{top:1725px;width:31px;height:61px;display:flex;align-items:center;justify-content:center}

/* how we do it */
.how-col{width:300px;text-align:center}
.how-box{left:449px;top:2224px;width:303px;height:286px;background:var(--white);box-shadow:0 2px 14px rgba(0,0,0,.14)}
.how-name{font-family:'Montserrat',sans-serif;font-weight:500;font-size:18px;line-height:30px;color:var(--ink)}
.how-text{font-size:15px;line-height:26px;color:var(--muted)}
.how-more{font-family:'Montserrat',sans-serif;font-weight:700;font-size:16px;color:var(--navy)}

/* footer */
.footer{left:0;top:2590px;width:1200px;height:482px}
.foot-head{top:2768px;font-family:'Montserrat',sans-serif;font-weight:600;font-size:18px;color:var(--white)}
.foot-links{left:394px;top:2814px;font-size:15.5px;line-height:26.8px;color:var(--white);list-style:none}
.foot-contact{left:567px;font-size:15.5px;color:var(--white);line-height:27px;display:flex;gap:10px}
.newsletter{left:851px;top:2822px;width:236px;height:43px;background:var(--white);border-radius:3px;overflow:hidden}
.newsletter span{position:absolute;left:12px;top:12px;font-size:15px;color:#888}
.newsletter .send{position:absolute;right:0;top:0;width:56px;height:43px;background:var(--orange);display:flex;align-items:center;justify-content:center}
.social{top:2903px;width:44px;height:44px;border-radius:50%}
.copyright{left:0;top:3004px;width:1200px;text-align:center;font-size:15.5px;color:var(--white)}
</style>
</head>
<body>

<!-- top bar -->
<svg class="abs topbar" width="1200" height="43" viewBox="0 0 1200 43" aria-hidden="true">
  <path d="M453 0 H1200 V43 H496 Z" fill="var(--navy)"/>
</svg>
<div class="abs topbar-item" style="left:526px">
  <span class="icon-dot"><svg width="16" height="12" viewBox="0 0 16 12"><rect x="0.5" y="0.5" width="15" height="11" rx="1" fill="var(--navy)"/><path d="M1 1 L8 7 L15 1" stroke="#fff" stroke-width="1.4" fill="none"/></svg></span>
  <span>Email:&nbsp; info@meridale-partners.example</span>
</div>
<div class="abs divider"></div>
<div class="abs topbar-item" style="left:900px">
  <span class="icon-dot"><svg width="16" height="16" viewBox="0 0 24 24"><path d="M6.6 10.8a15.1 15.1 0 0 0 6.6 6.6l2.2-2.2c.3-.3.7-.4 1-.2 1.1.4 2.3.6 3.6.6.6 0 1 .4 1 1V20c0 .6-.4 1-1 1A17 17 0 0 1 3 4c0-.6.4-1 1-1h3.5c.6 0 1 .4 1 1 0 1.3.2 2.5.6 3.6.1.3 0 .7-.2 1z" fill="var(--navy)"/></svg></span>
  <span>Call:&nbsp; 01 555 0142</span>
</div>

<!-- header -->
<div class="abs brand">
  <div class="brand-mark"></div>
  <div class="brand-name">MERIDALE<br>PARTNERS</div>
</div>
<div class="abs nav" style="left:510px">HOME</div>
<div class="abs nav" style="left:601px">SERVICES</div>
<div class="abs nav" style="left:721px">ABOUT US</div>
<div class="abs nav" style="left:842px">CONTACT US</div>
<div class="abs login">LOG IN</div>

<!-- hero -->
<svg class="abs hero" width="1200" height="720" viewBox="0 0 1200 720">
  <defs>
    <linearGradient id="heroFill" x1="0" y1="0" x2="1" y2="0.3">
      <stop offset="0" stop-color="#eef1f3"/>
      <stop offset="0.45" stop-color="#d9dfe4"/>
      <stop offset="0.75" stop-color="#8aa0b8"/>
      <stop offset="1" stop-color="#c9d2da"/>
    </linearGradient>
  </defs>
  <path d="M0 0 H1200 V515 Q600 891 0 515 Z" fill="url(#heroFill)" role="img" aria-label="Photo: smiling consultant in a blue suit holding a tablet in a bright office"/>
  <path d="M-10 512 Q600 900 1210 512" stroke="var(--navy)" stroke-width="18" fill="none"/>
</svg>
<div class="abs hero-welcome">WELCOME TO</div>
<div class="abs hero-title">MERIDALE<br>PARTNERS</div>
<div class="abs hero-sub">DATA ANALYTICS &amp; EPM CONSULTING SERVICES</div>
<div class="abs btn btn-start">GET STARTED</div>
<div class="abs dot" style="left:572px"></div>
<div class="abs dot" style="left:593px;background:var(--navy)"></div>
<div class="abs dot" style="left:614px"></div>

<!-- who we are -->
<div class="abs who-circle"></div>
<div class="abs who-photo" role="img" aria-label="Photo: laptop on a desk showing an analytics dashboard"></div>
<div class="abs who-title">WHO WE ARE <span class="rule"></span></div>
<p class="abs who-text">Meridale Partners is an exciting start-up in the Data Analytics and EPM space.&nbsp; Founded in 2019, MP specialise in the implementation and support of BI, EPM and Data Analytics business solutions, both in the Cloud and on-premise.</p>
<div class="abs btn btn-learn">LEARN MORE</div>

<!-- what we do -->
<div class="abs what"></div>
<div class="abs section-title" style="top:1462px;color:var(--white)">WHAT WE DO</div>
<div class="abs title-rule" style="top:1511px;background:var(--white)"></div>

<div class="abs card" style="left:111px">
  <div class="card-photo" role="img" aria-label="Photo: engineer in a hard hat in a workshop" style="background:linear-gradient(160deg,#cfd3d6,#8a8680 60%,#4c4b4a)"></div>
  <div class="card-shade"></div>
  <div class="card-name">Advise &amp; Architect</div>
  <div class="card-link">Learn More &rarr;</div>
</div>
<div class="abs card" style="left:451px">
  <div class="card-photo" role="img" aria-label="Photo: three colleagues talking together in an office" style="background:linear-gradient(160deg,#d8d2c8,#9a8670 60%,#6a5646)"></div>
  <div class="card-shade active"></div>
  <div class="card-name">Design &amp; Implement</div>
  <div class="card-link">Learn More &rarr;</div>
</div>
<div class="abs card" style="left:790px">
  <div class="card-photo" role="img" aria-label="Photo: laptop keyboard with glowing digital marketing icons" style="background:linear-gradient(160deg,#b8c2cc,#5e6b78 55%,#2d343c)"></div>
  <div class="card-shade"></div>
  <div class="card-name">Optimise &amp; Manage</div>
  <div class="card-link">Learn More &rarr;</div>
</div>
<div class="abs arrow-btn" style="left:0;background:var(--white)"><svg width="12" height="24" viewBox="0 0 12 24"><path d="M10 2 L2 12 L10 22" stroke="var(--orange)" stroke-width="1.8" fill="none"/></svg></div>
<div class="abs arrow-btn" style="left:1169px;background:var(--orange)"><svg width="12" height="24" viewBox="0 0 12 24"><path d="M2 2 L10 12 L2 22" stroke="#fff" stroke-width="1.8" fill="none"/></svg></div>

<!-- how we do it -->
<div class="abs section-title" style="top:2104px;color:var(--ink)">HOW WE DO IT</div>
<div class="abs title-rule" style="top:2153px;background:var(--navy)"></div>
<div class="abs how-box"></div>

<div class="abs how-col" style="left:85px;top:2249px">
  <svg width="76" height="76" viewBox="0 0 76 76" fill="none" stroke="var(--navy)" stroke-width="2">
    <rect x="22" y="22" width="32" height="32" rx="3"/><circle cx="38" cy="38" r="8"/>
    <path d="M30 22V8M38 22V4M46 22V8M30 54V68M38 54V72M46 54V68M22 30H8M22 38H4M22 46H8M54 30H68M54 38H72M54 46H68"/>
  </svg>
  <div class="how-name" style="margin-top:14px">Meridale Partners</div>
  <div class="how-text" style="margin-top:16px">Lorem ipsum dolor sit amet,<br>consectetur adipiscing elit,<br>sed do eiusmod</div>
  <div class="how-more" style="margin-top:15px">READ MORE</div>
</div>

<div class="abs how-col" style="left:450px;top:2249px">
  <svg width="76" height="76" viewBox="0 0 76 76" fill="none" stroke="var(--orange)" stroke-width="2">
    <rect x="6" y="14" width="64" height="46" rx="2"/><path d="M28 60 L24 72 H52 L48 60"/>
    <path d="M14 52V38M22 52V30M30 52V34M38 52V24"/><circle cx="56" cy="26" r="8"/><path d="M56 18V26H64"/><path d="M14 44 L28 40 L40 46 L62 40"/>
  </svg>
  <div class="how-name" style="margin-top:14px">Provide Analytics &amp; Enterprise<br>Performance Management</div>
  <div class="how-text" style="margin-top:11px">Lorem ipsum dolor sit amet,<br>consectetur adipiscing elit,</div>
  <div class="how-more" style="margin-top:15px;color:var(--orange)">READ MORE</div>
</div>

<div class="abs how-col" style="left:832px;top:2249px">
  <svg width="76" height="76" viewBox="0 0 76 76" fill="none" stroke="var(--navy)" stroke-width="2">
    <path d="M30 4 H54 V18 H44 L40 23 L38 18 H30 Z"/><rect x="12" y="30" width="22" height="18" rx="2"/><rect x="42" y="30" width="22" height="18" rx="2"/>
    <path d="M4 56 H72 M10 56 V72 M66 56 V72 M18 72 H58"/>
  </svg>
  <div class="how-name" style="margin-top:14px">Advisory &amp; consultancy</div>
  <div class="how-text" style="margin-top:16px">Lorem ipsum dolor sit amet,<br>consectetur adipiscing elit,<br>sed do eiusmod</div>
  <div class="how-more" style="margin-top:15px">READ MORE</div>
</div>

<!-- footer -->
<svg class="abs footer" width="1200" height="482" viewBox="0 0 1200 482" aria-hidden="true">
  <path d="M0 166 Q600 -150 1200 166 V482 H0 Z" fill="var(--black)"/>
  <path d="M-10 172 Q600 -156 1210 172" stroke="var(--navy)" stroke-width="16" fill="none"/>
</svg>
<div class="abs" style="left:111px;top:2826px;display:flex;align-items:center;gap:14px">
  <div style="width:56px;height:56px;border-radius:50%;background:var(--white)"></div>
  <div class="head-font" style="font-weight:700;font-size:20px;line-height:25px;color:var(--white)">MERIDALE<br>PARTNERS</div>
</div>
<div class="abs" style="left:111px;top:2916px;width:150px;height:32px;border:1.5px solid rgba(255,255,255,.7);border-radius:3px" role="img" aria-label="Technology partner badge"></div>

<div class="abs foot-head" style="left:394px">QUICK LINKS</div>
<ul class="abs foot-links"><li>Home</li><li>Services</li><li>About Us</li><li>Contact Us</li></ul>

<div class="abs foot-head" style="left:567px">CONTACT US</div>
<div class="abs foot-contact" style="top:2812px">
  <svg width="16" height="22" viewBox="0 0 16 22" style="margin-top:4px"><path d="M8 0a8 8 0 0 1 8 8c0 6-8 14-8 14S0 14 0 8a8 8 0 0 1 8-8z" fill="#fff"/><circle cx="8" cy="8" r="3" fill="#000"/></svg>
  <span>14 Harbour Row, Millbrook,<br>Ashford 2, A02 MP14</span>
</div>
<div class="abs foot-contact" style="top:2878px">
  <svg width="18" height="18" viewBox="0 0 24 24" style="margin-top:4px"><path d="M6.6 10.8a15.1 15.1 0 0 0 6.6 6.6l2.2-2.2c.3-.3.7-.4 1-.2 1.1.4 2.3.6 3.6.6.6 0 1 .4 1 1V20c0 .6-.4 1-1 1A17 17 0 0 1 3 4c0-.6.4-1 1-1h3.5c.6 0 1 .4 1 1 0 1.3.2 2.5.6 3.6.1.3 0 .7-.2 1z" fill="#fff"/></svg>
  <span>01 555 0142</span>
</div>
<div class="abs foot-contact" style="top:2916px">
  <svg width="18" height="14" viewBox="0 0 16 12" style="margin-top:7px"><rect width="16" height="12" rx="1" fill="#fff"/><path d="M1 1 L8 7 L15 1" stroke="#000" stroke-width="1.4" fill="none"/></svg>
  <span>info@meridalepartners.example</span>
</div>

<div class="abs foot-head" style="left:851px">SIGN UP FOR NEWSLETTER</div>
<div class="abs newsletter">
  <span>Email Address</span>
  <div class="send"><svg width="18" height="13" viewBox="0 0 16 12"><rect width="16" height="12" rx="1" fill="#fff"/><path d="M1 1 L8 7 L15 1" stroke="var(--orange)" stroke-width="1.4" fill="none"/></svg></div>
</div>
<div class="abs social" style="left:980px;background:var(--navy)" role="img" aria-label="Social profile link"></div>
<div class="abs social" style="left:1041px;border:2px solid var(--navy)" role="img" aria-label="Social profile link"></div>

<div class="abs copyright">&copy;Copyrights 2022 Meridale Partners &nbsp;|&nbsp;&nbsp; All Rights Reserved</div>

</body>
</html>
```